Keystone Trench Co Business Card*

Looking for a professional, clean and crisp business card

I am in the underground utilities industry and am just looking for a really impressive business card. I would like our card to be white with our symbol crisp and clear with it protruding. I also have a business partner that will require his name and info on the card once the design is set. I would like to have our website info on the card which is;
http://keystonetrenchco.example/

Contact Information for Business Card

Website, contact name, number and email

```html
<!DOCTYPE html>
<html lang="en">
<head>
<meta charset="utf-8">
<title>Keystone Trench Co – Business Card</title>
<link href="https://fonts.googleapis.com/css2?family=Roboto:wght@400;500;700&family=Oswald:wght@500&display=swap" rel="stylesheet">
<style>
  :root {
    --backdrop: #e4e4e4;
    --card-white: #ffffff;
    --card-dark: #2f2f2f;
    --accent-blue: #3a5bb0;
    --ink: #3a3a3a;
    --ink-soft: #6a6a6a;
    --rule: #9a9a9a;
    --mark-light: #f2f2f2;
  }
  * { margin: 0; padding: 0; box-sizing: border-box; }
  html, body { width: 1200px; height: 801px; overflow: hidden; background: var(--backdrop); }
  .stage { position: relative; width: 1200px; height: 801px; }

  .card {
    position: absolute;
    width: 520px;
    height: 297px;
    top: 252px;
    border-bottom: 4px solid var(--accent-blue);
    box-shadow: 0 10px 24px rgba(0,0,0,0.18);
    overflow: hidden;
  }
  .card--front { left: 50px; background: var(--card-white); }
  .card--back { left: 630px; background: var(--card-dark); }

  /* front */
  .brand {
    position: absolute; left: 36px; top: 0; width: 200px; height: 100%;
    display: flex; align-items: center; gap: 10px;
  }
  .brand__dot { width: 18px; height: 18px; border-radius: 50%; background: var(--accent-blue); flex: none; }
  .brand__name {
    font-family: "Oswald", sans-serif; font-weight: 500; font-size: 22px;
    color: #1c1c1c; text-transform: uppercase; letter-spacing: 0.5px; line-height: 1.15;
  }
  .divider { position: absolute; left: 250px; top: 92px; width: 1px; height: 110px; background: var(--rule); }
  .contact { position: absolute; left: 272px; top: 86px; font-family: "Roboto", sans-serif; }
  .contact__name { font-size: 21px; font-weight: 700; color: var(--accent-blue); }
  .contact__role { font-size: 12px; color: var(--ink-soft); margin-top: 2px; }
  .contact__list { list-style: none; margin-top: 22px; }
  .contact__item {
    display: flex; align-items: center; gap: 8px;
    font-size: 12.5px; color: var(--ink); line-height: 20px;
  }
  .contact__item svg { width: 12px; height: 12px; flex: none; }
  .contact__link { color: var(--accent-blue); }

  /* back */
  .back-mark {
    position: absolute; top: 62px; left: 0; width: 100%;
    text-align: center; font-family: "Oswald", sans-serif; font-weight: 500;
    font-size: 40px; color: var(--mark-light); text-transform: uppercase; letter-spacing: 1px;
  }
  .back-scene {
    position: absolute; left: 0; bottom: 0; width: 100%; height: 150px;
    background: linear-gradient(180deg, rgba(47,47,47,0) 0%, #3b3b3b 40%, #5e5e5e 100%);
  }
</style>
</head>
<body>
<main class="stage">
  <section class="card card--front" aria-label="Card front">
    <div class="brand">
      <span class="brand__dot"></span>
      <span class="brand__name">Keystone<br>Trench Co</span>
    </div>
    <div class="divider"></div>
    <div class="contact">
      <p class="contact__name">Dale Marrick</p>
      <p class="contact__role">Owner</p>
      <ul class="contact__list">
        <li class="contact__item">
          <svg viewBox="0 0 12 12"><path d="M3 1 L5 3.5 L4 5 Q5 7 7 8 L8.5 7 L11 9 L9.5 11 Q4 10.5 1 3 Z" fill="var(--accent-blue)"/></svg>
          555-014-2288(DIGS)
        </li>
        <li class="contact__item">
          <svg viewBox="0 0 12 12"><rect x="1" y="2.5" width="10" height="7" fill="none" stroke="var(--accent-blue)" stroke-width="1.3"/><path d="M1 2.5 L6 6.5 L11 2.5" fill="none" stroke="var(--accent-blue)" stroke-width="1.3"/></svg>
          dale@keystonetrenchco.example
        </li>
        <li class="contact__item">
          <svg viewBox="0 0 12 12"><circle cx="6" cy="6" r="5" fill="var(--accent-blue)"/><path d="M1 6 H11 M6 1 Q3 6 6 11 M6 1 Q9 6 6 11" fill="none" stroke="#fff" stroke-width="0.8"/></svg>
          <span>www.<span class="contact__link">keystonetrenchco.example</span></span>
        </li>
      </ul>
    </div>
  </section>

  <section class="card card--back" aria-label="Card back">
    <p class="back-mark">Keystone Trench Co</p>
    <div class="back-scene" role="img" aria-label="Grey mountain range illustration along the lower part of the card"></div>
  </section>
</main>
</body>
</html>
```